Design and Renovation Company Luxury Business Card

I want to create a luxury business card for a Design and Renovation Firm . We will use our current logo. The company name is 528BUILDA. We do not want anything standard. We need a very unique concept.
Please see uploaded inspiration. I really like the textured paper option. I would like the card to be thick with debossing, and/or embossing options. The logo has orange in it but I would like to see the card with and without the orange. I think the orange may make the company feel less high-end. The goal is to elevate the logo not match its vibe per se of the logo. We want something very unique, not standard at all!
I would like a space for :
Logo,
Name,
Position,
Email,
Office number,
Website Address,
Business Address,
Thank you!
Have fun!
Target Market(s)
Home owners Age 35 +
Industry/Entity Type
Design and Renovation
Contact Information for Business Card
Logo, Name, Position, Email, Office number, Website Address, Business Address,.
Colors
Designer to choose colors to be used in the design.
Requirements
Must have
- A luxury designer feel. Must be black or dark grey but open to other luxury ideas.
Nice to have
- Gold, silver, black embossing or debossing. Textured paper design.
Should not have
- A cheap look and feel.

```html
<!DOCTYPE html>
<html lang="en">
<head>
<meta charset="UTF-8">
<title>528BUILDA Business Card</title>
<link href="https://fonts.googleapis.com/css2?family=Montserrat:wght@400;500;700&display=swap" rel="stylesheet">
<style>
  :root {
    --bg: #2a2a2a;
    --card: #1c1c1c;
    --card-back: #1f1f1f;
    --orange: #f7941d;
    --white: #ffffff;
    --muted: #e6e6e6;
    --deboss: #111111;
  }
  * { margin: 0; padding: 0; box-sizing: border-box; }
  html, body {
    width: 1200px; height: 801px; overflow: hidden;
    background: var(--bg);
    font-family: "Montserrat", Arial, sans-serif;
  }
  .stage {
    width: 1200px; height: 801px;
    display: flex; align-items: center; justify-content: center; gap: 40px;
  }
  .card {
    position: relative;
    width: 540px; height: 309px;
    border-radius: 18px;
    overflow: hidden;
    border-bottom: 3px solid var(--orange);
  }
  .card--front { background: var(--card); }
  .card--back { background: var(--card-back); }

  /* Front: company name */
  .company {
    position: absolute; left: 40px; top: 70px;
    width: 280px; height: 148px;
    display: flex; align-items: center; justify-content: center;
  }
  .company__name {
    font-weight: 500; font-size: 30px; letter-spacing: 1px;
    color: var(--white); line-height: 1;
  }

  .divider {
    position: absolute; left: 335px; top: 70px;
    width: 1px; height: 148px; background: var(--orange);
  }

  .contact {
    position: absolute; left: 350px; top: 62px;
    color: var(--muted); font-size: 10.5px; line-height: 1.35;
  }
  .contact__name { color: var(--orange); font-weight: 700; font-size: 19px; line-height: 1.1; }
  .contact__title { font-size: 11px; margin-bottom: 10px; }
  .contact__address { margin-bottom: 8px; }
  .contact__row { display: flex; align-items: center; gap: 6px; }
  .contact__row svg { width: 10px; height: 10px; flex: none; }

  .band {
    position: absolute; left: 0; bottom: 30px;
    width: 100%; height: 20px;
  }

  /* Back: debossed company name */
  .back-name {
    position: absolute; inset: 0;
    display: flex; align-items: center; justify-content: center;
  }
  .back-name__text {
    font-weight: 500; font-size: 56px; letter-spacing: 2px;
    color: var(--deboss); line-height: 1;
  }
</style>
</head>
<body>
<main class="stage">

  <section class="card card--front" aria-label="Business card front">
    <div class="company">
      <span class="company__name">528BUILDA</span>
    </div>

    <div class="divider"></div>

    <div class="contact">
      <p class="contact__name">Daniel Carter</p>
      <p class="contact__title">Managing Director</p>
      <p class="contact__address">415 Maple Grove Ave, #112<br>Brookfield, OH 430471</p>
      <p class="contact__row">
        <svg viewBox="0 0 10 10"><path d="M2 1 L4 3 L3 4 Q4 6 6 7 L7 6 L9 8 L8 9 Q4 9 1 5 Q1 2 2 1 Z" fill="var(--orange)"/></svg>
        555-318-0247
      </p>
      <p class="contact__row">
        <svg viewBox="0 0 10 10"><rect x="0.5" y="2" width="9" height="6.5" fill="var(--orange)"/><path d="M0.5 2 L5 5.5 L9.5 2" stroke="var(--card)" stroke-width="1" fill="none"/></svg>
        hello@528builda.com
      </p>
      <p class="contact__row">
        <svg viewBox="0 0 10 10"><circle cx="5" cy="5" r="4.5" fill="var(--orange)"/><path d="M0.5 5 H9.5 M5 0.5 Q2.5 5 5 9.5 M5 0.5 Q7.5 5 5 9.5" stroke="var(--card)" stroke-width="0.7" fill="none"/></svg>
        www.528builda.com
      </p>
    </div>

    <svg class="band" viewBox="0 0 540 20" preserveAspectRatio="none">
      <polygon points="0,0 300,0 290,20 0,20" fill="var(--orange)"/>
      <polygon points="307,0 540,0 540,20 297,20" fill="var(--white)"/>
    </svg>
  </section>

  <section class="card card--back" aria-label="Business card back">
    <div class="back-name">
      <span class="back-name__text">528BUILDA</span>
    </div>
  </section>

</main>
</body>
</html>
```